Re-design and craft the perfect CV platform

We are building a CV-based platform designed to connect employees and employers, with a strong focus on individual users. As we're just starting out, we're looking to have our platform and logo redesigned to better reflect our vision
https://app.zelvorhire.com/
Colors like in the logo attached
#87C032 #6A6E71 #618930 - also you can add more colors if you like.
https://app.zelvorhire.com/dashboard - This page would be nice if you plan it, like personal Bio dashboard. Attached picture (Dashboard wanted) one idea from how we would like to be, but we are open for new professional ideas/solutions.
https://app.zelvorhire.com/posts - On this page we want to be showed the jobs posted. Attached one picture about our idea (jobs page wanted)
https://app.zelvorhire.com/profile - design something nice.
Only Photoshop, Illustrator or Figma
Other pictures from the app attached (as looking right now)

Target Market(s)

Job seekers, HR, Recruiters

Industry/Entity Type

HR Tech

Number of Pages Required

5+ page

Colors
00AB8E
00BBA5
67D7C9
C6EFE9
E9F9F6

```html
<!DOCTYPE html>
<html lang="en">
<head>
<meta charset="utf-8">
<title>ZELVORHIRE – Profile Dashboard</title>
<link href="https://fonts.googleapis.com/css2?family=Poppins:wght@300;400;500;600;700;800&display=swap" rel="stylesheet">
<style>
:root{
  --teal:#00AB8E;
  --teal-2:#00BBA5;
  --teal-3:#67D7C9;
  --teal-4:#C6EFE9;
  --teal-5:#E9F9F6;
  --slate:#6A6E71;
  --ink:#5b5f62;
  --text:#6f7376;
  --page:#f2f2f2;
  --white:#ffffff;
  --line:#e3e3e3;
}
*{box-sizing:border-box;margin:0;padding:0}
html,body{width:1200px;height:817px;overflow:hidden}
body{background:var(--page);font-family:"Poppins",sans-serif;color:var(--text);position:relative}

.topbar{position:absolute;left:0;top:0;width:1200px;height:90px;background:var(--white)}
.brand{position:absolute;left:63px;top:32px;display:flex;align-items:center;gap:8px}
.brand-dot{width:22px;height:22px;background:var(--teal);border-radius:50%}
.brand-name{font-weight:600;font-size:22px;letter-spacing:.5px;color:var(--teal)}
.nav{position:absolute;right:64px;top:29px;display:flex;align-items:center;gap:7px}
.nav-btn{width:101px;height:33px;border-radius:2px;display:flex;align-items:center;justify-content:center;gap:4px;font-size:14px;font-weight:600}
.nav-btn.is-active{background:var(--teal);color:var(--white)}
.nav-btn.is-ghost{border:1.5px solid var(--slate);color:var(--slate)}
.nav-avatar{width:33px;height:33px;border-radius:50%;background:var(--teal);display:flex;align-items:center;justify-content:center;margin-left:1px}

.card{position:absolute;top:101px;height:687px;border-radius:17px;background:var(--white);overflow:hidden}

.profile{left:63px;width:271px;background:var(--slate);color:var(--white)}
.profile-photo{position:absolute;left:40px;top:20px;width:193px;height:193px;border-radius:50%;border:4px solid var(--teal);background:radial-gradient(circle at 50% 40%,#d8dee3 0%,#9aa5ad 55%,#3b3f44 100%)}
.profile-name{position:absolute;top:219px;left:0;width:271px;text-align:center;font-weight:800;font-size:26px;letter-spacing:-.4px}
.profile-role{position:absolute;top:252px;left:0;width:271px;text-align:center;font-size:14px;letter-spacing:.6px}
.facts{position:absolute;left:32px;top:285px;width:232px;font-size:13.8px;line-height:21.4px}
.facts dt{float:left;width:75px;clear:left}
.facts dd{white-space:nowrap}
.side-block{position:absolute;left:32px;width:225px}
.side-head{display:flex;align-items:center;gap:10px;font-weight:600;font-size:17px;text-transform:uppercase}
.side-icon{width:30px;height:30px;border-radius:50%;background:var(--white);display:flex;align-items:center;justify-content:center;flex:none}
.side-text{font-size:13.8px;line-height:21px;margin-top:6px}
.side-text b{font-weight:600}

.overview{left:351px;width:519px}
.section{position:absolute;left:0;width:519px;padding:22px 0 0 16px}
.section + .section{border-top:1px solid var(--line)}
.section-head{display:flex;align-items:center;gap:10px;font-weight:500;font-size:17px;color:var(--ink);text-transform:uppercase}
.section-icon{width:30px;height:30px;border-radius:50%;background:var(--teal);display:flex;align-items:center;justify-content:center;flex:none}
.section-body{font-size:13.6px;margin-top:13px;padding-right:18px}
.about .section-body{line-height:21.4px}
.education .section-body{line-height:23.2px}
.skills .section-body{line-height:23.8px}
.notes .section-body{line-height:21.4px}

.postings{left:887px;width:249px;padding:24px 19px}
.postings-title{font-weight:600;font-size:21.5px;color:var(--ink)}
.job{position:absolute;left:19px;width:212px}
.job-title{font-weight:600;font-size:13.8px;color:var(--ink)}
.job-desc{font-size:11.8px;line-height:18px;margin-top:3px}
.apply{display:flex;align-items:center;justify-content:center;width:101px;height:33px;background:var(--teal);color:var(--white);font-size:14.5px;border-radius:2px;margin-top:14px}
</style>
</head>
<body>
<header class="topbar">
  <div class="brand"><span class="brand-dot"></span><span class="brand-name">ZELVORHIRE</span></div>
  <nav class="nav">
    <div class="nav-btn is-active">
      <svg width="13" height="11" viewBox="0 0 13 11"><rect x="0" y="2.5" width="13" height="8.5" rx="1.5" fill="#fff"/><rect x="4" y="0" width="5" height="3" rx="1" fill="none" stroke="#fff" stroke-width="1.3"/></svg>Jobs</div>
    <div class="nav-btn is-ghost">
      <svg width="11" height="12" viewBox="0 0 11 12"><rect x="1" y="0" width="9" height="12" rx="1" fill="#6A6E71"/></svg>CV</div>
    <div class="nav-avatar"><svg width="14" height="15" viewBox="0 0 14 15"><circle cx="7" cy="4" r="3.6" fill="#fff"/><path d="M0 15c0-4 3-6.5 7-6.5s7 2.5 7 6.5z" fill="#fff"/></svg></div>
  </nav>
</header>

<aside class="card profile">
  <div class="profile-photo" role="img" aria-label="Profile photo of the candidate"></div>
  <h1 class="profile-name">MAREK DELVAN</h1>
  <p class="profile-role">Software Engineer</p>
  <dl class="facts">
    <dt>Age:</dt><dd>35</dd>
    <dt>Gender:</dt><dd>Male</dd>
    <dt>Phone:</dt><dd>+08 555 014 2739</dd>
  </dl>
  <div class="side-block" style="top:386px">
    <div class="side-head"><span class="side-icon"><svg width="16" height="16" viewBox="0 0 16 16"><circle cx="8" cy="5" r="3" fill="#00AB8E"/><path d="M3 13c0-3 2-4.5 5-4.5s5 1.5 5 4.5z" fill="#00AB8E"/></svg></span>Work Experience</div>
    <p class="side-text">Years of Work Experience:&nbsp; 15+</p>
  </div>
  <div class="side-block" style="top:470px">
    <div class="side-head"><span class="side-icon"><svg width="16" height="14" viewBox="0 0 16 14"><rect x="0" y="0" width="10" height="8" rx="2" fill="#00AB8E"/><rect x="6" y="5" width="10" height="8" rx="2" fill="#00AB8E" stroke="#fff" stroke-width="1"/></svg></span>Languages</div>
    <p class="side-text"><b>Hungarian: 100%</b>&nbsp;&nbsp;&nbsp; <b>English:</b> 80%</p>
  </div>
  <div class="side-block" style="top:555px">
    <div class="side-head"><span class="side-icon"><svg width="16" height="13" viewBox="0 0 16 13"><rect x="0" y="0" width="16" height="13" rx="2" fill="#00AB8E"/><circle cx="5" cy="5.5" r="2" fill="#fff"/><rect x="9" y="4" width="5" height="1.5" fill="#fff"/><rect x="9" y="7" width="5" height="1.5" fill="#fff"/></svg></span>Driver's License</div>
    <p class="side-text">License Type: Full, Class B (valid for cars and light vehicles).</p>
  </div>
</aside>

<main class="card overview">
  <section class="section about" style="top:0;height:172px">
    <h2 class="section-head"><span class="section-icon"><svg width="14" height="15" viewBox="0 0 14 15"><circle cx="7" cy="4" r="3.3" fill="#fff"/><path d="M1 15c0-4 2.5-6 6-6s6 2 6 6z" fill="#fff"/></svg></span>About Me</h2>
    <p class="section-body">Experienced and adaptable software engineer with over 15 years in the tech industry. Skilled in developing innovative solutions for complex problems, with a focus on efficiency, user experience, and reliability. Known for strong teamwork, attention to detail, and a commitment to</p>
  </section>
  <section class="section education" style="top:172px;height:156px">
    <h2 class="section-head"><span class="section-icon"><svg width="17" height="12" viewBox="0 0 17 12"><path d="M8.5 0L17 4 8.5 8 0 4z" fill="#fff"/><path d="M3.5 6v3.5c1.5 1.5 8.5 1.5 10 0V6l-5 2.5z" fill="#fff"/></svg></span>Education</h2>
    <p class="section-body">Qualification: Master’s in Computer<br>Institution: University of Technology, 2010.<br>Additional Certifications: Certified Agile Lead, Norvale IT Automation</p>
  </section>
  <section class="section skills" style="top:328px;height:203px">
    <h2 class="section-head"><span class="section-icon"><svg width="16" height="16" viewBox="0 0 16 16"><circle cx="8" cy="8" r="5" fill="none" stroke="#fff" stroke-width="2.5" stroke-dasharray="2.6 1.3"/><circle cx="8" cy="8" r="2" fill="#fff"/></svg></span>Skills</h2>
    <p class="section-body">Programming Languages: Vantor, Quillon, Brisklet, DataQL.<br>Frameworks: Stemwork, Reflux, Nodix.<br>Database Management: Keystore, GraniteDB<br>Project Management Tools: Taskgrid, Boardly, Flowpad.<br>Soft Skills: Problem-solving, Team Leadership, Communication,</p>
  </section>
  <section class="section notes" style="top:531px;height:156px">
    <h2 class="section-head"><span class="section-icon"><svg width="14" height="15" viewBox="0 0 14 15"><path d="M7 1c3 0 4.5 2.3 4.5 5v3l1.5 2H1l1.5-2V6C2.5 3.3 4 1 7 1z" fill="#fff"/><circle cx="7" cy="13" r="1.7" fill="#fff"/></svg></span>Notifications</h2>
    <p class="section-body">New job opportunities available in your field. Stay updated with notifications tailored to your professional interests!</p>
  </section>
</main>

<aside class="card postings">
  <h2 class="postings-title">JOB POSTINGS</h2>
  <article class="job" style="top:84px">
    <h3 class="job-title">Senior Full Stack Developer</h3>
    <p class="job-desc">Looking for an experienced developer proficient in front-end and back-end technologies.</p>
    <a class="apply">Apply</a>
  </article>
  <article class="job" style="top:245px">
    <h3 class="job-title">IT Project Manager</h3>
    <p class="job-desc">Lead project planning, execut ion, and closing for diverse IT projects across departments.</p>
    <a class="apply">Apply</a>
  </article>
  <article class="job" style="top:400px">
    <h3 class="job-title">UX/UI Designer</h3>
    <p class="job-desc">Join our team to design intuitive user interfaces and enhance user experience for our software.</p>
    <a class="apply">Apply</a>
  </article>
</aside>
</body>
</html>
```